Remote Game Console (Tavlin) Wpf/Web UI

A complete interface for a second generation remote console tool to administer PC games. Will primarily run as a desktop application with future plans of running within a browser.

All materials are supplied as a guide only, but the designer is free to build what they would find easy to use. We're engineers so help us out with a good user experience.

The first version of Tavlin Emberhold was released in March 2009 supporting Skyrend: Iron Platoon 2. It was updated later in the year to support the expansion, SRIP2: Kestrel. Crest of Valour followed in late 2010 and Skyrend 3 support in October 2011. All games are based on MORV's Emberhold engine. http://dravek.example/tavlin-emberhold/

Tavlin 2 will eventually support all games, working more along the lines of a framework for others to expand upon. While ultimately having a similar function as Tavlin Emberhold, Tavlin 2 has been completely rewritten and shares no similarities internally.

The primary focus of the application is to display details about a users rented Game Server. A user can kick, ban and chat with players in their servers. A user can alter the settings of their game server, setting the time of a round or the game servers name for instance.

We have a forum dedicated to this competition that users of our software can give general feedback about the existing (Tavlin Emberhold) software, such as what they hate etc. http://www.dravek.example/forumvb/forumdisplay.php?35-UI-Competition

You can find similar software with much cooler looking UI's at http://www.ip2xz.example/ and http://sk3xz.example/

The techy details:

Tavlin 2 can run locally or connect and login to a hosted version of the software (internally we call this a Local Interface or Remote Interface). Logging into a remote server requires an IP, port, username and password. Beyond the initial local/remote selection the UI can function identically.

1 Instance of the software has a single Local (no login required) or Remote (ip/port/username/password required) Interface.

1 Instance has many Packages. A package is an extension to the software that the user can install. A package can be an update to Tavlin 2 itself, a plugin or a config.

1 Instance has many Options. We are partial to Nuvex Lumas Options panel. Something similar which would allow us to expand would be neat.

1 Instance has many languages.

1 Interface has many Game Connections. A game connection requires an ip, port and password to connect and authenticate. A game connection has a name, maximum players allowed to connect, a game type (e.g iron platoon 2, crest of valour, skyrend 3).

1 Game Connection has many plugins. A plugin extends the functionality of the software in the background.

1 Game Connection has many players. A player has a name, country, score, ping, kills, deaths and other variables depending on the type of Game connected to.

1 Game Connection has many bans. A ban is a record of a player, the players identifying information, a small description of why the ban was put in place as well as an expiry time (e.g. banned for 2 weeks or permanently banned)

1 Game Connection has many settings. These settings can vary dramatically depending on the Game connected to.

1 Interface has many Groups. A group has a name any many permissions.

1 Group has many Accounts.

1 Account has many players.
Updates

Reason: Uploaded wireframes. I work a lot and this is my side project. I thought I would have wireframes the next day of this project, but it didn't end up like that. All current submissions have been the first iteration of my software reskinned, not the next version.

Target Market(s)

First Person Shooter PC game administrators

Industry/Entity Type

Software

Requirements
Must have
• Tavlin 2 has a primitive natural language parser for converting free text into commands for the program. An online functional example is available at http://labs.venta.example/the-thrifty-helper/ (check down the bottom). The design should incorporate a text box throughout the application for users to enter commands in. As the user types this could be passed to display what will happen once the user executes the command

Generally people will be minimizing their games to kick or ban people from their servers. The UI design should be easy enough to navigate quickly.

A UI that can handle multiple languages. Our primary market is Germany.

The UI must be usable at 1024x768. It should be designed to take up the maximum window/browser space.
Nice to have
• Responsive design that scales to any resolution. We have a large mobile user base that could benefit from a UI that scales well on lower resolutions.

Tavlin 2 has no set logo as of yet, though we will continue using the smiley found at http://dravek.example - we only have a 100 by 100px png of this image though. If a larger version is supplied you'll receive a virtual cookie and a thank you! The logo will probably end up as a variation of that found on http://dravek.example/tavlin-emberhold/ but we'll go through the exact process for this at a later date

```html
<!DOCTYPE html>
<html lang="en">
<head>
<meta charset="utf-8">
<title>Tavlin Emberhold</title>
<link rel="stylesheet" href="https://fonts.googleapis.com/css2?family=Noto+Sans:wght@400;700&display=swap">
<style>
:root{
  --bg:#0d0d0e;
  --panel:#1a1a1a;
  --panel-line:#3a3a3a;
  --text:#d8d8d8;
  --muted:#bdbdbd;
  --orange:#e8631e;
  --orange-row:#c9531c;
  --blue-row:#8ea0b4;
  --beige-row:#d9d3ac;
  --link:#3aa0e0;
}
*{box-sizing:border-box;margin:0;padding:0}
html,body{width:1200px;height:1058px;overflow:hidden;background:var(--bg)}
body{font-family:"Noto Sans",sans-serif;color:var(--text);font-size:11px}
.app{position:absolute;left:0;top:0;width:1024px;height:903px;transform:scale(1.171875);transform-origin:0 0;background:var(--bg);overflow:hidden}
.backdrop{position:absolute;inset:0;background:radial-gradient(ellipse at 70% 70%,#2e2a26 0%,#161514 45%,#0a0a0a 100%)}
.titlebar{position:absolute;left:0;top:0;width:1024px;height:46px;background:linear-gradient(#3a3a3a,#1a1a1a)}
.app-title{position:absolute;left:44px;top:16px;font-size:17px;color:#f0f0f0}
.app-dot{position:absolute;left:20px;top:22px;width:10px;height:10px;border-radius:50%;background:#6a6f75}
.win-btns{position:absolute;right:26px;top:12px;display:flex;gap:4px}
.win-btns span{width:17px;height:17px;background:#e6e6e6;border-radius:2px;color:#111;font-weight:700;font-size:13px;line-height:17px;text-align:center}
.menubar{position:absolute;left:12px;top:53px;display:flex;gap:13px;font-size:12px;color:#e0e0e0}
.toolbar{position:absolute;left:16px;top:80px;display:flex;align-items:center;gap:10px}
.server-select{position:absolute;left:111px;top:79px;width:402px;height:20px;background:#fff;border:1px solid #888;color:#111;font-size:11px;display:flex;align-items:center;padding-left:4px;gap:5px}
.server-mark{width:50px;height:12px;background:#555}
.tick{width:10px;height:10px;background:#8bc34a;border:1px solid #5d8a2c}
.drop{margin-left:auto;width:16px;height:18px;background:#ddd;border-left:1px solid #aaa;display:flex;align-items:center;justify-content:center}
.autoconnect{position:absolute;left:527px;top:79px;width:161px;height:21px;background:#fff;border:1px solid #888;color:#111;display:flex;align-items:center;gap:6px;padding-left:5px;font-size:11px}
.statusline{position:absolute;left:19px;top:116px;font-size:11px;color:#e6e6e6}
.statusline span{position:absolute;white-space:nowrap}
.tabs{position:absolute;left:9px;top:141px;width:1006px;height:28px;background:linear-gradient(#f4f4f4,#c9c9c9);border-radius:3px;font-size:11px;color:#222}
.tabs span{position:absolute;top:7px;white-space:nowrap}
.tab-active{left:10px!important;top:2px!important;width:57px;height:24px;background:linear-gradient(#4a4a4a,#1a1a1a);color:#fff;border-radius:3px;text-align:center;line-height:24px}
.roster{position:absolute;top:182px;width:493px;height:476px;background:var(--panel);border:1px solid var(--panel-line)}
.roster.left{left:15px}
.roster.right{left:513px}
.row{display:grid;grid-template-columns:37px 47px 105px 48px 51px 41px 34px 48px 36px 44px;height:18px;line-height:18px;font-size:11px;color:var(--muted)}
.row>span{padding-left:5px;white-space:nowrap;overflow:hidden}
.row.head{height:22px;line-height:22px;background:linear-gradient(#4a4a4a,#262626);color:#e0e0e0}
.row.head>span{border-right:1px solid #151515}
.team{height:18px;line-height:18px;margin-top:8px;margin-bottom:3px;color:var(--orange);padding-left:12px;white-space:nowrap;overflow:hidden}
.row.blue{background:var(--blue-row);color:#fff}
.row.beige{background:var(--beige-row);color:#fff}
.row.hot{background:var(--orange-row);color:#fff}
.row .name{padding-left:8px}
.flag{display:inline-block;width:10px;height:7px;margin-right:1px;vertical-align:-1px}
.de{background:linear-gradient(#111 33%,#d22 33% 66%,#f5c400 66%)}
.it{background:linear-gradient(90deg,#2a9a3a 33%,#fff 33% 66%,#d22 66%)}
.sum{color:var(--orange);margin-top:0}
.player-card{position:absolute;left:10px;top:668px;width:1004px;height:192px;background:rgba(20,20,20,.55);border-top:1px solid #2c2c2c}
.card-title{position:absolute;left:20px;top:17px;font-size:13px;color:var(--orange)}
.field{position:absolute;left:20px;font-size:11px;color:#ccc;width:600px;white-space:nowrap}
.field label{display:inline-block;width:63px;text-align:right}
.field i{position:absolute;left:96px;top:-2px;width:526px;height:16px;background:#3b3b3b;border:1px solid #4a4a4a}
.actions{position:absolute;left:650px;top:41px;width:324px;height:142px;background:#2b2b2b;border:1px solid #444;border-radius:4px}
.act-tabs{position:absolute;left:658px;top:20px;display:flex;gap:2px}
.act-tabs span{height:20px;line-height:20px;padding:0 18px;border-radius:3px 3px 0 0;font-size:11px}
.act-tabs .on{background:var(--orange);color:#fff}
.act-tabs .off{background:#d8d4b8;color:#222}
.opt{position:absolute;font-size:11px;color:#bbb;display:flex;align-items:center;gap:9px;white-space:nowrap}
.radio{width:11px;height:11px;border-radius:50%;background:#161616;border:1px solid #555}
.radio.on{background:radial-gradient(#fff 30%,#161616 40%)}
.reason-label{position:absolute;left:136px;top:10px;color:var(--orange)}
.reason-box{position:absolute;left:136px;top:28px;width:148px;height:20px;background:#fff;border:1px solid #999}
.time-box{position:absolute;left:11px;top:111px;width:35px;height:20px;background:#1e1e1e;border:1px solid #555}
.unit-box{position:absolute;left:53px;top:111px;width:102px;height:20px;background:#3a3a3a;border:1px solid #555;color:#ccc;padding-left:7px;line-height:18px}
.discharge{position:absolute;left:168px;top:111px;width:142px;height:21px;border-radius:5px;background:linear-gradient(#f07a35,#d4501a);color:#fff;text-align:center;line-height:21px;font-size:11px;white-space:nowrap}
.close-x{position:absolute;left:958px;top:14px;width:15px;height:15px;background:#eee;color:#111;font-weight:700;text-align:center;line-height:15px;border-radius:2px;font-size:11px}
.build{position:absolute;left:995px;top:876px;color:#eee;font-size:12px}
</style>
</head>
<body>
<div class="app">
  <div class="backdrop" role="img" aria-label="Dark atmospheric game-scene backdrop in charcoal and warm brown tones"></div>

  <header class="titlebar">
    <span class="app-dot"></span>
    <span class="app-title">Tavlin Emberhold</span>
    <div class="win-btns"><span>–</span><span>+</span><span>×</span></div>
  </header>

  <nav class="menubar"><span>File</span><span>Tools</span><span>Help</span></nav>

  <div class="toolbar">
    <svg width="24" height="22" viewBox="0 0 24 22"><path d="M12 2 1 12h3v9h6v-6h4v6h6v-9h3z" fill="#bbb"/></svg>
    <svg width="20" height="18" viewBox="0 0 20 18"><path d="M1 9 10 1v5h9v6h-9v5z" fill="#888"/></svg>
    <svg width="20" height="18" viewBox="0 0 20 18"><path d="M19 9 10 1v5H1v6h9v5z" fill="#888"/></svg>
  </div>
  <div class="server-select"><span class="server-mark"></span><span class="tick"></span>[32/32] Tavlin[kx-org.example - Deine Community !<span class="drop"><svg width="8" height="5"><path d="M0 0h8L4 5z" fill="#333"/></svg></span></div>
  <div class="autoconnect"><span class="tick"></span>Automatically Connect</div>

  <div class="statusline">
    <span style="left:0">Rush - Vandermoor</span>
    <span style="left:107px">Round: 1/2</span>
    <span style="left:177px;color:#777">⟳ ⬇</span>
    <span style="left:215px;color:var(--link)">Accepting Players</span>
    <span style="left:360px">Version: 471930 (R17)</span>
    <span style="left:497px;color:var(--link)">0.5.8.1</span>
  </div>

  <div class="tabs">
    <span class="tab-active">Players</span>
    <span style="left:92px">Chat</span>
    <span style="left:164px">Map</span>
    <span style="left:237px">Events</span>
    <span style="left:308px">Lists</span>
    <span style="left:381px">Server Settings</span>
    <span style="left:489px">Plugins</span>
    <span style="left:561px">Accounts</span>
    <span style="left:632px">Console</span>
    <span style="left:704px">Parent Layer Control</span>
  </div>

  <section class="roster left">
    <div class="row head"><span>ID#</span><span>Tags</span><span>Name</span><span>Squad</span><span>Kit</span><span>Score</span><span>Kills</span><span>Deaths</span><span>K/Dr</span><span>Ping</span></div>
    <div class="team">16 - Attackers - 83 Tickets ---------------------------------------------------------------------------------------------------</div>
    <div class="row blue"><span>32</span><span></span><span class="name">Holvrik</span><span>Alpha</span><span>Medic</span><span>330</span><span>4</span><span>2</span><span>2,00</span><span>98</span></div>
    <div class="row"><span><i class="flag de"></i>16</span><span></span><span class="name">Murk_Vessa</span><span>Bravo</span><span>Assault</span><span>0</span><span>0</span><span>0</span><span>0,00</span><span>135</span></div>
    <div class="row"><span><i class="flag it"></i>19</span><span></span><span class="name">Rook4gate</span><span>Delta</span><span>Engineer</span><span>100</span><span>2</span><span>2</span><span>2.50</span><span>116</span></div>
    <div class="row"><span>32</span><span></span><span class="name">Holvrik</span><span>Alpha</span><span>Medic</span><span>330</span><span>4</span><span>2</span><span>2,00</span><span>98</span></div>
    <div class="row"><span>16</span><span></span><span class="name">Murk_Vessa</span><span>Bravo</span><span>Assault</span><span>0</span><span>0</span><span>0</span><span>0,00</span><span>135</span></div>
    <div class="row"><span>19</span><span></span><span class="name">Rook4gate</span><span>Delta</span><span>Engineer</span><span>100</span><span>2</span><span>2</span><span>2.50</span><span>116</span></div>
    <div class="row blue"><span><i class="flag de"></i>32</span><span></span><span class="name">Holvrik</span><span>Alpha</span><span>Medic</span><span>330</span><span>4</span><span>2</span><span>2,00</span><span>98</span></div>
    <div class="row"><span><i class="flag it"></i>16</span><span></span><span class="name">Murk_Vessa</span><span>Bravo</span><span>Assault</span><span>0</span><span>0</span><span>0</span><span>0,00</span><span>135</span></div>
    <div class="row"><span>19</span><span></span><span class="name">Rook4gate</span><span>Delta</span><span>Engineer</span><span>100</span><span>2</span><span>2</span><span>2.50</span><span>116</span></div>
    <div class="row"><span>32</span><span></span><span class="name">Holvrik</span><span>Alpha</span><span>Medic</span><span>330</span><span>4</span><span>2</span><span>2,00</span><span>98</span></div>
    <div class="row hot"><span>16</span><span></span><span class="name">Murk_Vessa</span><span>Bravo</span><span>Assault</span><span>0</span><span>0</span><span>0</span><span>0,00</span><span>135</span></div>
    <div class="row"><span><i class="flag de"></i>19</span><span></span><span class="name">Rook4gate</span><span>Delta</span><span>Engineer</span><span>100</span><span>2</span><span>2</span><span>2.50</span><span>116</span></div>
    <div class="row"><span><i class="flag it"></i>32</span><span></span><span class="name">Holvrik</span><span>Alpha</span><span>Medic</span><span>330</span><span>4</span><span>2</span><span>2,00</span><span>98</span></div>
    <div class="row"><span>16</span><span></span><span class="name">Murk_Vessa</span><span>Bravo</span><span>Assault</span><span>0</span><span>0</span><span>0</span><span>0,00</span><span>135</span></div>
    <div class="row"><span><i class="flag de"></i>19</span><span></span><span class="name">Rook4gate</span><span>Delta</span><span>Engineer</span><span>100</span><span>2</span><span>2</span><span>2.50</span><span>116</span></div>
    <div class="row"><span><i class="flag it"></i>32</span><span></span><span class="name">Holvrik</span><span>Alpha</span><span>Medic</span><span>330</span><span>4</span><span>2</span><span>2,00</span><span>98</span></div>
    <div class="row"><span>16</span><span></span><span class="name">Murk_Vessa</span><span>Bravo</span><span>Assault</span><span>0</span><span>0</span><span>0</span><span>0,00</span><span>135</span></div>
    <div class="row"><span>19</span><span></span><span class="name">Rook4gate</span><span>Delta</span><span>Engineer</span><span>100</span><span>2</span><span>2</span><span>2.50</span><span>116</span></div>
    <div class="row"><span>32</span><span></span><span class="name">Holvrik</span><span>Alpha</span><span>Medic</span><span>330</span><span>4</span><span>2</span><span>2,00</span><span>98</span></div>
    <div class="row"><span>16</span><span></span><span class="name">Murk_Vessa</span><span>Bravo</span><span>Assault</span><span>0</span><span>0</span><span>0</span><span>0,00</span><span>135</span></div>
    <div class="row"><span>19</span><span></span><span class="name">Rook4gate</span><span>Delta</span><span>Engineer</span><span>100</span><span>2</span><span>2</span><span>2.50</span><span>116</span></div>
    <div class="row sum"><span></span><span></span><span class="name">Averages</span><span></span><span>Recon</span><span>155,63</span><span>1,69</span><span>1,31</span><span>1,08</span><span>130</span></div>
    <div class="row sum"><span></span><span></span><span class="name">Totals</span><span></span><span>6R,2M,</span><span>2490</span><span>27</span><span>21</span><span>17,33</span><span></span></div>
  </section>

  <section class="roster right">
    <div class="row head"><span>ID#</span><span>Tags</span><span>Name</span><span>Squad</span><span>Kit</span><span>Score</span><span>Kills</span><span>Deaths</span><span>K/Dr</span><span>Ping</span></div>
    <div class="team">16 - Attackers - 83 Tickets ---------------------------------------------------------------------------------------------------</div>
    <div class="row"><span><i class="flag de"></i>32</span><span></span><span class="name">Holvrik</span><span>Alpha</span><span>Medic</span><span>330</span><span>4</span><span>2</span><span>2,00</span><span>98</span></div>
    <div class="row"><span><i class="flag it"></i>16</span><span></span><span class="name">Murk_Vessa</span><span>Bravo</span><span>Assault</span><span>0</span><span>0</span><span>0</span><span>0,00</span><span>135</span></div>
    <div class="row"><span>19</span><span></span><span class="name">Rook4gate</span><span>Delta</span><span>Engineer</span><span>100</span><span>2</span><span>2</span><span>2.50</span><span>116</span></div>
    <div class="row"><span>32</span><span></span><span class="name">Holvrik</span><span>Alpha</span><span>Medic</span><span>330</span><span>4</span><span>2</span><span>2,00</span><span>98</span></div>
    <div class="row beige"><span>16</span><span></span><span class="name">Murk_Vessa</span><span>Bravo</span><span>Assault</span><span>0</span><span>0</span><span>0</span><span>0,00</span><span>135</span></div>
    <div class="row"><span>19</span><span></span><span class="name">Rook4gate</span><span>Delta</span><span>Engineer</span><span>100</span><span>2</span><span>2</span><span>2.50</span><span>116</span></div>
    <div class="row"><span><i class="flag it"></i>32</span><span></span><span class="name">Holvrik</span><span>Alpha</span><span>Medic</span><span>330</span><span>4</span><span>2</span><span>2,00</span><span>98</span></div>
    <div class="row"><span>16</span><span></span><span class="name">Murk_Vessa</span><span>Bravo</span><span>Assault</span><span>0</span><span>0</span><span>0</span><span>0,00</span><span>135</span></div>
    <div class="row"><span>19</span><span></span><span class="name">Rook4gate</span><span>Delta</span><span>Engineer</span><span>100</span><span>2</span><span>2</span><span>2.50</span><span>116</span></div>
    <div class="row"><span>32</span><span></span><span class="name">Holvrik</span><span>Alpha</span><span>Medic</span><span>330</span><span>4</span><span>2</span><span>2,00</span><span>98</span></div>
    <div class="row"><span>16</span><span></span><span class="name">Murk_Vessa</span><span>Bravo</span><span>Assault</span><span>0</span><span>0</span><span>0</span><span>0,00</span><span>135</span></div>
    <div class="row beige"><span><i class="flag it"></i>19</span><span></span><span class="name">Rook4gate</span><span>Delta</span><span>Engineer</span><span>100</span><span>2</span><span>2</span><span>2.50</span><span>116</span></div>
    <div class="row"><span>32</span><span></span><span class="name">Holvrik</span><span>Alpha</span><span>Medic</span><span>330</span><span>4</span><span>2</span><span>2,00</span><span>98</span></div>
    <div class="row"><span>16</span><span></span><span class="name">Murk_Vessa</span><span>Bravo</span><span>Assault</span><span>0</span><span>0</span><span>0</span><span>0,00</span><span>135</span></div>
    <div class="row"><span><i class="flag de"></i>19</span><span></span><span class="name">Rook4gate</span><span>Delta</span><span>Engineer</span><span>100</span><span>2</span><span>2</span><span>2.50</span><span>116</span></div>
    <div class="row"><span><i class="flag de"></i>32</span><span></span><span class="name">Holvrik</span><span>Alpha</span><span>Medic</span><span>330</span><span>4</span><span>2</span><span>2,00</span><span>98</span></div>
    <div class="row"><span>16</span><span></span><span class="name">Murk_Vessa</span><span>Bravo</span><span>Assault</span><span>0</span><span>0</span><span>0</span><span>0,00</span><span>135</span></div>
    <div class="row hot"><span>19</span><span></span><span class="name">Rook4gate</span><span>Delta</span><span>Engineer</span><span>100</span><span>2</span><span>2</span><span>2.50</span><span>116</span></div>
    <div class="row"><span>32</span><span></span><span class="name">Holvrik</span><span>Alpha</span><span>Medic</span><span>330</span><span>4</span><span>2</span><span>2,00</span><span>98</span></div>
    <div class="row"><span>16</span><span></span><span class="name">Murk_Vessa</span><span>Bravo</span><span>Assault</span><span>0</span><span>0</span><span>0</span><span>0,00</span><span>135</span></div>
    <div class="row"><span>19</span><span></span><span class="name">Rook4gate</span><span>Delta</span><span>Engineer</span><span>100</span><span>2</span><span>2</span><span>2.50</span><span>116</span></div>
    <div class="row sum"><span></span><span></span><span class="name">Averages</span><span></span><span>Recon</span><span>155,63</span><span>1,69</span><span>1,31</span><span>1,08</span><span>130</span></div>
    <div class="row sum"><span></span><span></span><span class="name">Totals</span><span></span><span>6R,2M,</span><span>2490</span><span>27</span><span>21</span><span>17,33</span><span></span></div>
  </section>

  <section class="player-card">
    <div class="card-title">Holvrik (Germany)</div>
    <div class="field" style="top:41px"><label>GW Guid:</label><i></i></div>
    <div class="field" style="top:65px"><label>IP:</label><i></i></div>
    <div class="field" style="top:89px"><label>MV Guid:</label><i></i></div>
    <div class="field" style="top:113px;width:640px">Inventory:&nbsp; KRV LMG, TR - 208 , Light Weight Combat Equipment, Improved Demolitions, Alternate Weapon Package</div>

    <div class="act-tabs"><span class="on">SRIP2</span><span class="off">Guardwall</span></div>
    <span class="close-x">×</span>
    <div class="actions">
      <div class="opt" style="left:10px;top:12px"><i class="radio on"></i>Kill</div>
      <div class="opt" style="left:10px;top:34px"><i class="radio"></i>Kick</div>
      <div class="opt" style="left:10px;top:56px"><i class="radio"></i>Permanently ban</div>
      <div class="opt" style="left:10px;top:78px"><i class="radio"></i>Temporary ban</div>
      <div class="opt" style="left:10px;top:97px">Time</div>
      <div class="reason-label">Reason</div>
      <div class="reason-box"></div>
      <div class="opt" style="left:142px;top:62px"><i class="radio on"></i>Name</div>
      <div class="opt" style="left:212px;top:62px"><i class="radio"></i>IP</div>
      <div class="opt" style="left:254px;top:62px"><i class="radio"></i>Guide</div>
      <div class="time-box"></div>
      <div class="unit-box">Minutes</div>
      <div class="discharge">Dishonarably Discharge</div>
    </div>
  </section>

  <div class="build">X6</div>
</div>
</body>
</html>
```